Crimson Ridge Footrace Co.

We need a website (wordpress) design for a new website that we will be launching. This is for a new trail racing series in Canada.
We recently had a logo designed so want to incorporate the colours of the logo on the website design. Especially the dark blue, green and orange.
Websites that we like for comparison of trail running race themes are:
https://www.mosslinerunning.com/
https://www.bramblestridecup.com/
http://www.quarrypathcircuit.ca/
https://www.cobaltcreekchase.com/
http://www.dunmoorrunningtour.com/

Target Market(s)

Outdoor trail runners

Coding

Coded - Design and coding required

Number of Pages Required

4 page

Font styles to use
Sans Serif

Colors
0255a3
33b8a4
f37122

Requirements
Must have
• There will be a main page with eye catching design noting what we do. Page 2 and 3 will be for each race in the series. Page 1 will be a specific race, and page 2 with be for another race. page 3 and 4 will be for future races that we add so that each race has their own page.
• Our races all take place in the mountains, so using graphics including mountains, rivers, trees is all a requirement for us.
• Our logo is attached, we want to use the colours of the logo in the website design.
Nice to have
• Outdoor theme is a nice to have. We like wood and earth tone colours, and pictures/graphics of runners and mountains and trees.
• There are 4 people involved in our organization. We'd like a photo and brief blurb of each of us, similar to how this website did their layout: https://www.mosslinerunning.com/

```html
<!DOCTYPE html>
<html lang="en">
<head>
<meta charset="utf-8">
<title>Crimson Ridge Footrace Co.</title>
<link href="https://fonts.googleapis.com/css2?family=Raleway:wght@400;600;700;800&family=Lato:wght@400;700&display=swap" rel="stylesheet">
<style>
:root{
  --blue:#0255a3;
  --navy:#0a3f8f;
  --green:#33b8a4;
  --orange:#f37122;
  --text:#5a5a5a;
  --footer:#1a1816;
  --white:#ffffff;
  --card:#f1f1f1;
}
*{box-sizing:border-box;margin:0;padding:0}
html,body{width:1200px;height:3586px;overflow:hidden}
body{position:relative;font-family:'Lato',sans-serif;color:var(--text);background:var(--white)}
.abs{position:absolute}
.photo{position:absolute;display:block}
/* header */
.hero{position:absolute;left:0;top:0;width:1200px;height:705px;background:linear-gradient(160deg,#2f3326 0%,#4a4a36 30%,#5a5640 55%,#3a3628 80%,#6b5a3c 100%)}
.brand-small{position:absolute;left:100px;top:24px;width:180px;color:var(--white);font-family:'Raleway',sans-serif;font-weight:800;font-size:14px;line-height:1.25;text-transform:uppercase}
.nav{position:absolute;left:645px;top:48px;display:flex;gap:26px;font-family:'Raleway',sans-serif;font-size:15px;font-weight:600;color:var(--white)}
.nav .active{color:var(--orange)}
.hero-title{position:absolute;left:300px;top:380px;width:600px;text-align:center;color:var(--white);font-family:'Raleway',sans-serif;font-weight:800;font-size:58px;line-height:1.05;text-transform:uppercase}
/* features */
.feature{position:absolute;top:808px;width:294px;height:232px;color:var(--white);padding:28px 24px}
.feature h3{font-family:'Raleway',sans-serif;font-weight:600;font-size:21px;margin:14px 0 10px}
.feature p{font-size:12.5px;line-height:1.6;font-weight:700}
.feature .more{position:absolute;right:-18px;bottom:-14px;background:#111;color:var(--white);font-size:13px;padding:9px 28px;clip-path:polygon(14% 0,100% 0,86% 100%,0 100%)}
.f-run{left:96px;background:var(--navy)}
.f-adv{left:440px;background:var(--green)}
.f-evt{left:782px;background:var(--orange)}
/* about */
.about{position:absolute;left:0;top:1109px;width:1200px;height:516px;background:linear-gradient(180deg,#22221f,#2f2e28 60%,#3a3830)}
.kicker{font-family:'Raleway',sans-serif;font-weight:700;font-size:14px;color:var(--orange);text-transform:uppercase}
.about h2{font-family:'Raleway',sans-serif;font-weight:700;font-size:26px;color:var(--green);margin:10px 0 18px}
.about p{font-size:13.5px;line-height:1.95;color:#e2e2e2}
.btn{display:inline-block;background:var(--blue);color:var(--white);font-family:'Raleway',sans-serif;font-weight:700;font-size:14px;border-radius:24px;padding:13px 30px;text-transform:uppercase}
/* events */
.section-title{position:absolute;left:0;width:1200px;text-align:center;font-family:'Raleway',sans-serif;font-weight:600;font-size:25px;color:var(--green)}
.event-date{display:flex;align-items:center;gap:14px;font-family:'Raleway',sans-serif;font-size:21px;color:var(--orange);text-transform:uppercase}
.event-date::after{content:"";width:150px;height:1px;background:var(--orange)}
.event h3{font-family:'Raleway',sans-serif;font-weight:700;font-size:26px;color:var(--blue);margin:28px 0 22px;text-transform:uppercase}
.event p{font-size:15px;line-height:1.9;color:var(--text)}
/* team */
.team{position:absolute;left:0;top:2658px;width:1200px;height:497px;background:linear-gradient(170deg,#2a2925,#3b3a33 50%,#24231f)}
.team-title{color:var(--orange);font-weight:700;text-transform:uppercase}
.member{position:absolute;top:2835px;width:490px;height:180px;background:var(--card)}
.member .portrait{position:absolute;left:26px;top:-10px;width:116px;height:130px;border:6px solid #ddd}
.member h4{position:absolute;left:160px;top:20px;font-family:'Raleway',sans-serif;font-weight:700;font-size:16px;color:var(--blue);text-transform:uppercase}
.member .role{position:absolute;left:160px;top:46px;font-size:12px;color:#9a9a9a;background:#e3e3e3;padding:3px 40px 3px 14px}
.member p{position:absolute;left:160px;top:86px;width:300px;font-size:13px;line-height:1.85;color:#9a9a9a}
.member .social{position:absolute;left:44px;top:142px;display:flex;gap:10px}
.dot{width:22px;height:22px;border-radius:50%;border:1px solid #bbb;background:#fff}
.arrow{position:absolute;top:2902px}
/* footer */
.footer{position:absolute;left:0;top:3155px;width:1200px;height:431px;background:var(--footer);color:#ddd}
.footer h5{font-family:'Raleway',sans-serif;font-weight:600;font-size:18px;color:var(--orange);text-transform:uppercase;margin-bottom:18px}
.footer small{font-size:11.5px;line-height:1.75;display:block}
.f-brand{font-family:'Raleway',sans-serif;font-weight:800;font-size:22px;line-height:1.1;color:var(--white);text-transform:uppercase}
.input{width:264px;height:36px;background:#fff;color:#999;font-size:12px;padding:10px 14px;margin:22px 0 14px}
.sub{display:inline-block;background:var(--blue);color:#fff;font-family:'Raleway',sans-serif;font-weight:700;font-size:13px;padding:9px 28px;text-transform:uppercase}
.contact li,.links li{list-style:none;font-size:12.5px;font-weight:700;margin-bottom:22px;display:flex;gap:14px;align-items:flex-start}
.links li{margin-bottom:16px}
.circ{width:36px;height:36px;border-radius:50%}
.copy{position:absolute;left:0;top:365px;width:1200px;border-top:1px solid #3a3733;text-align:center;font-size:12px;font-weight:700;color:#ddd;padding-top:22px}
</style>
</head>
<body>

<header>
  <div class="hero photo" role="img" aria-label="Photo of trail runners racing through a shaded forest path"></div>
  <div class="brand-small">Crimson Ridge<br>Footrace Co.</div>
  <nav class="nav">
    <span class="active">HOME</span><span>ABOUT</span><span>SERVICES</span><span>BLOG</span><span>CONTACT</span>
  </nav>
  <div class="hero-title">Crimson Ridge<br>Footrace Co.</div>
</header>

<section class="features">
  <div class="feature f-run">
    <svg width="70" height="48" viewBox="0 0 70 48"><path d="M6 14h22M2 24h22M10 34h18" stroke="#fff" stroke-width="4" stroke-linecap="round"/><path d="M34 24h28M50 12l14 12-14 12" stroke="#fff" stroke-width="5" fill="none" stroke-linecap="round" stroke-linejoin="round"/></svg>
    <h3>Run</h3>
    <p>Lorem ipsum dolor sit amet, conset sadi elitr, sed diam nonumy eirmod tempor invidunt ut labore et dolore .</p>
    <span class="more">View Details</span>
  </div>
  <div class="feature f-adv">
    <svg width="60" height="52" viewBox="0 0 60 52"><rect x="2" y="2" width="56" height="48" fill="none" stroke="#fff" stroke-width="3"/><path d="M6 46 L24 16 L34 30 L42 22 L54 46 Z" fill="#fff"/></svg>
    <h3>Adventure</h3>
    <p>Lorem ipsum dolor sit amet, conset sadi elitr, sed diam nonumy eirmod tempor invidunt ut labore et dolore.</p>
    <span class="more">View Details</span>
  </div>
  <div class="feature f-evt">
    <svg width="60" height="56" viewBox="0 0 60 56"><rect x="3" y="8" width="54" height="45" rx="3" fill="none" stroke="#fff" stroke-width="3"/><rect x="3" y="8" width="54" height="11" fill="#fff"/><path d="M16 2v12M44 2v12" stroke="#fff" stroke-width="4"/><g fill="#fff"><rect x="10" y="25" width="8" height="7"/><rect x="22" y="25" width="8" height="7"/><rect x="34" y="25" width="8" height="7"/><rect x="46" y="25" width="6" height="7"/><rect x="10" y="37" width="8" height="7"/><rect x="22" y="37" width="8" height="7"/><rect x="34" y="37" width="8" height="7"/></g></svg>
    <h3>Events</h3>
    <p>Lorem ipsum dolor sit amet, conset sadi elitr, sed diam nonumy eirmod tempor invidunt ut labore et dolore.</p>
    <span class="more">View Details</span>
  </div>
</section>

<section class="about">
  <div class="photo" style="left:110px;top:85px;width:476px;height:312px;background:linear-gradient(170deg,#a7bccf 0%,#8ba0a8 30%,#6f8a6a 55%,#4b5a3c 80%,#3a3f2e 100%);box-shadow:0 6px 20px rgba(0,0,0,.5)" role="img" aria-label="Video still of a runner on a rocky mountain ridge above a green valley"></div>
  <svg class="abs" style="left:332px;top:225px" width="32" height="32" viewBox="0 0 32 32"><path d="M8 4 L28 16 L8 28 Z" fill="#fff"/></svg>
  <div class="abs" style="left:638px;top:92px;width:450px">
    <div class="kicker">About Us</div>
    <h2>Welcome to Crimson Ridge</h2>
    <p>Sed ut perspiciatis unde omnis iste natus error sit voluptatem accusantium doloremque laudantium, totam rem aperiam, eaque ipsa quae ab illo inventore veritatis et quasi architecto beatae vitae dicta sunt explicabo. Nemo enim ipsam voluptatem quia voluptas sit aspernatur aut odit aut fugit, sed quia consequuntur magni dolores eos qui ratione voluptatem sequi nesciunt.</p>
    <div style="margin-top:24px"><span class="btn">Read More</span></div>
  </div>
</section>

<section class="events">
  <h2 class="section-title" style="top:1710px">Events</h2>
  <div class="photo" style="left:93px;top:1793px;width:480px;height:292px;background:linear-gradient(160deg,#b9cbe0 0%,#e6ecf2 30%,#7d9a5a 65%,#5c6a3e 100%)" role="img" aria-label="Photo of trail runners climbing a grassy slope below snowy peaks"></div>
  <div class="event abs" style="left:628px;top:1805px;width:470px">
    <div class="event-date">May 2018</div>
    <h3>Lorem ipsum dolor sit amet</h3>
    <p>Sed ut perspiciatis unde omnis iste natus error sit voluptatem accusantium doloremque laudantium, totam rem aperiam, eaque ipsa quae ab illo inventore veritatis et quasi architecto beatae vitae dicta sunt explicabo.</p>
  </div>
  <div class="event abs" style="left:131px;top:2180px;width:460px">
    <div class="event-date">April 2018</div>
    <h3>Lorem ipsum dolor sit amet</h3>
    <p>Sed ut perspiciatis unde omnis iste natus error sit voluptatem accusantium doloremque laudantium, totam rem aperiam, eaque ipsa quae ab illo inventore veritatis et quasi architecto beatae vitae dicta sunt explicabo.</p>
  </div>
  <div class="photo" style="left:628px;top:2158px;width:479px;height:318px;background:linear-gradient(170deg,#c8d6e4 0%,#9aa59a 40%,#7b7a6c 70%,#5c5a4e 100%)" role="img" aria-label="Photo of a runner in an orange shirt leaping across mossy rocks"></div>
  <div class="abs" style="left:528px;top:2530px"><span class="btn" style="padding:14px 30px;font-size:16px">View All</span></div>
</section>

<section class="team" role="img" aria-label="Background photo of runners on a dusky mountain trail"></section>
<h2 class="section-title team-title" style="top:2736px">Meet Our Team</h2>
<svg class="arrow" style="left:56px" width="20" height="30" viewBox="0 0 20 30"><path d="M16 3 L4 15 L16 27" stroke="#fff" stroke-width="3" fill="none"/></svg>
<svg class="arrow" style="left:1122px" width="20" height="30" viewBox="0 0 20 30"><path d="M4 3 L16 15 L4 27" stroke="#fff" stroke-width="3" fill="none"/></svg>
<div class="member" style="left:96px">
  <div class="portrait photo" style="background:linear-gradient(180deg,#d8cfc6,#a99888)" role="img" aria-label="Portrait photo of Marcus Holloway"></div>
  <div class="social"><span class="dot"></span><span class="dot"></span><span class="dot"></span></div>
  <h4>Marcus Holloway</h4><span class="role">Lorem ipsum</span>
  <p>Lorem ipsum dolor sit amet, consectetur adipisicing elit, sed do eiusd tempor incididunt</p>
</div>
<div class="member" style="left:610px">
  <div class="portrait photo" style="background:linear-gradient(180deg,#e2dad2,#b5a593)" role="img" aria-label="Portrait photo of Devin Ashgrove"></div>
  <div class="social"><span class="dot"></span><span class="dot"></span><span class="dot"></span></div>
  <h4>Devin Ashgrove</h4><span class="role">Lorem ipsum</span>
  <p>Lorem ipsum dolor sit amet, consectetur adipisicing elit, sed do eiusd tempor incididunt</p>
</div>

<footer class="footer">
  <div class="abs" style="left:100px;top:80px;width:240px">
    <div class="f-brand">Crimson Ridge<br>Footrace Co.</div>
    <small style="margin-top:18px">At vero eos et accusamus et iusto odio dignissimos ducimus qui blanditiis</small>
    <div style="display:flex;gap:16px;margin-top:20px">
      <span class="circ" style="background:var(--blue)"></span><span class="circ" style="background:#1d9bf0"></span><span class="circ" style="background:#b8862c"></span>
    </div>
  </div>
  <div class="abs" style="left:375px;top:88px;width:280px">
    <h5>Signup for Newsletter</h5>
    <small>On the other hand, we denounce with righteous indignation and dislike men who are so beguiled</small>
    <div class="input">Enter Your Email</div>
    <span class="sub">Subscribe</span>
  </div>
  <div class="abs contact" style="left:717px;top:84px;width:240px">
    <h5>Contact Us</h5>
    <ul>
      <li><svg width="12" height="16" viewBox="0 0 12 16"><path d="M6 0a6 6 0 0 1 6 6c0 4-6 10-6 10S0 10 0 6a6 6 0 0 1 6-6z" fill="#fff"/><circle cx="6" cy="6" r="2.2" fill="#1a1816"/></svg><span>2207 Larchmont Lane,<br>Cedar Hollow, BC</span></li>
      <li><svg width="14" height="14" viewBox="0 0 14 14"><path d="M3 0l3 3-2 2c1 2 3 4 5 5l2-2 3 3-2 3C6 14 0 8 0 3z" fill="#fff"/></svg><span>604 555 0193</span></li>
      <li><svg width="15" height="11" viewBox="0 0 15 11"><rect width="15" height="11" fill="#fff"/><path d="M0 0l7.5 6L15 0" stroke="#1a1816" fill="none"/></svg><span>hello@crimsonridgefootrace.ca</span></li>
    </ul>
  </div>
  <div class="abs links" style="left:975px;top:84px;width:160px">
    <h5>Quick Links</h5>
    <ul>
      <li>» &nbsp;Home</li><li>» &nbsp;About</li><li>» &nbsp;Service</li><li>» &nbsp;Blog</li><li>» &nbsp;Contact</li>
    </ul>
  </div>
  <div class="copy">Copyrights © 2018 . Allrights Reserved.</div>
</footer>

</body>
</html>
```